BRAMBLEFORD CONSTRUCTIONS B-Card

I currently have a b-card design but will be removing the image (tree) from the logo and have text only.
I want the card to be classy and strong within the building and construction industry.
I will be using Spot UV on the cards as per the attached examples. I will also send through some sketched ideas that I have in mind.
The color blue is similar to the image (No. 6) attached images

Target Market(s)

middle to maturre aged.
Home Owners / Renovators and Builders

Industry/Entity Type

Construction

Contact Information for Business Card

BRAMBLEFORD CONSTRUCTIONS
Name: Gareth Pennick
Title: Project Manager
Mobile: 0427 351 804
Office: (08) 9316 5172
Address: 47C Corvell Street, Malaga WA 6090
Email: info@bramblefordhomes.com.au
PO Box: 3817 Malaga WA 6944

Colors
0592cd
33a6d7
85cae6
1b1b1b

Requirements
Must have
• 1. It must have spot UV on the front of card, maybe back of card too
• 2. I really like the blue on image 6. (or at least a really cool electric blue against the charcoal grey background)
• 3. The font must be slimline and modern. Easy to read
• 4. There must be no black used on the card... Only greys and dark charcoal greys
• 5. Use only the text from the logo "Brambleford Constructions" Not the image of the tree. I am wanting the b-cards to be more masculine.
Nice to have
• 1. I like the design concept on image 6. but happy to see what else you can do with the Spot UV
• 2. Unless you have a really cool idea of the image of the tree (from previous logo) Spot UV somewhere in the design concept thats original and different then I am keen to see what you come up with
• 3. Try changing the color of the logo eg. full white or Blue and white
• 4. Another option is to have the Brambleford Logo on the front of card with the spot UV in the background of text which we specialise in eg, Roofing, Ceiling, Insulation, Gutter Guards, Electrical, Insurance etc and we can add or reduce items as required. Similar to image 12.
Should not have
• Do not include the image of the tree from previous logo. unless you have a really cool idea of Spot UV somewhere in the design concept thats original and different.

```html
<!DOCTYPE html>
<html lang="en">
<head>
<meta charset="utf-8">
<title>Brambleford Constructions – Business Card</title>
<link href="https://fonts.googleapis.com/css2?family=Jost:wght@400;500&family=Source+Sans+3:wght@400&display=swap" rel="stylesheet">
<style>
  :root {
    --backdrop: #5b4b3d;
    --card-white: #ffffff;
    --brand-blue: #1a5aa5;
    --name-blue: #14529c;
    --charcoal: #1b1b1b;
    --text-dark: #2b2b2b;
    --text-grey: #5a5a5a;
  }
  * { margin: 0; padding: 0; box-sizing: border-box; }
  html, body {
    width: 1200px; height: 987px; overflow: hidden;
    background: var(--backdrop);
  }
  .stage { position: relative; width: 1200px; height: 987px; }

  .card {
    position: absolute; left: 299px; width: 610px; height: 348px;
    overflow: hidden;
  }
  .card-front { top: 157px; background: var(--card-white); }
  .card-back { top: 527px; background: var(--brand-blue); }

  .name-accent {
    position: absolute; left: 0; top: 60px; width: 11px; height: 43px;
    background: var(--brand-blue);
  }
  .holder {
    position: absolute; left: 35px; top: 55px;
    font-family: "Jost", sans-serif;
  }
  .holder-name {
    font-size: 24px; font-weight: 500; color: var(--name-blue);
    line-height: 30px;
  }
  .holder-title {
    font-size: 17px; font-weight: 400; color: var(--text-dark);
    line-height: 22px;
  }
  .address {
    position: absolute; left: 35px; top: 124px;
    font-family: "Jost", sans-serif; font-size: 16px; line-height: 20px;
    color: var(--text-grey); font-style: normal;
  }
  .contacts {
    position: absolute; left: 35px; top: 219px; list-style: none;
    font-family: "Jost", sans-serif; color: var(--text-grey);
  }
  .contacts li {
    display: flex; align-items: center; height: 23px; font-size: 16px;
  }
  .contacts li.email { font-size: 14px; }
  .contacts svg { width: 14px; height: 14px; margin-right: 8px; flex: none; }

  .company-name {
    position: absolute; white-space: nowrap;
    font-family: "Jost", sans-serif; font-weight: 500;
  }
  .company-name-front {
    right: 40px; top: 236px; font-size: 22px; line-height: 28px;
    color: var(--brand-blue);
  }
  .company-name-back {
    left: 0; right: 0; top: 150px; text-align: center;
    font-size: 34px; line-height: 42px; color: var(--card-white);
  }

  .bottom-band { position: absolute; left: 0; bottom: 0; width: 610px; height: 348px; }

  .services {
    position: absolute; left: 0; right: 0; top: 271px; text-align: center;
    font-family: "Source Sans 3", sans-serif; font-size: 16.5px; line-height: 21px;
    color: var(--card-white);
  }
</style>
</head>
<body>
<main class="stage">

  <section class="card card-front" aria-label="Business card front">
    <div class="name-accent"></div>
    <div class="holder">
      <p class="holder-name">Gareth Pennick</p>
      <p class="holder-title">Project Manager</p>
    </div>
    <address class="address">
      47C Corvell Street<br>
      Malaga WA 6090<br>
      PO Box:<br>
      3817 Malaga WA 6944
    </address>
    <ul class="contacts">
      <li>
        <svg viewBox="0 0 24 24" aria-hidden="true"><path fill="#1a5aa5" d="M6.6 10.8a15.1 15.1 0 0 0 6.6 6.6l2.2-2.2a1 1 0 0 1 1-.25 11.4 11.4 0 0 0 3.6.6 1 1 0 0 1 1 1V20a1 1 0 0 1-1 1A17 17 0 0 1 3 4a1 1 0 0 1 1-1h3.5a1 1 0 0 1 1 1c0 1.25.2 2.45.6 3.6a1 1 0 0 1-.25 1z"/></svg>
        (08) 9316 5172
      </li>
      <li>
        <svg viewBox="0 0 24 24" aria-hidden="true"><rect x="6" y="1.5" width="12" height="21" rx="2" fill="none" stroke="#1a5aa5" stroke-width="2.4"/><rect x="10" y="18" width="4" height="1.8" fill="#1a5aa5"/></svg>
        0427 351 804
      </li>
      <li class="email">
        <svg viewBox="0 0 24 24" aria-hidden="true"><rect x="2" y="5" width="20" height="14" fill="#1a5aa5"/><path d="M2.5 5.5 12 13l9.5-7.5" fill="none" stroke="#fff" stroke-width="1.6"/></svg>
        info@bramblefordhomes.com.au
      </li>
    </ul>
    <p class="company-name company-name-front">Brambleford Constructions</p>
    <svg class="bottom-band" viewBox="0 0 610 348" aria-hidden="true">
      <polygon points="0,330 394,325 390,348 0,348" fill="#1a5aa5"/>
      <polygon points="401,325 610,325 610,348 397,348" fill="#1b1b1b"/>
    </svg>
  </section>

  <section class="card card-back" aria-label="Business card back">
    <p class="company-name company-name-back">Brambleford Constructions</p>
    <p class="services">
      Roofing &bull; Ceiling &bull; Insulation &bull; Gutter Guards<br>
      Electrical &bull; Insurance etc
    </p>
  </section>

</main>
</body>
</html>
```